Website Design for a holiday home letting busines

We require a redesign of our present website www.pinebrookstays.com. We want the website to stand out and look professional and clean to make holiday hunters want to book a caravan or lodge holiday with us. Our logo is red however we DO NOT want the website to be red. We want a natural colour scheme.

The final design should communicate that we are a professional company to book with.

On the home page we require;
Overview of company
Photo
Search box for holiday (check in)
Late Deals
Reviews
News

We would like the following pages designed; home page, available dates page, caravans page, content page.

The website should be responsive for smart phones. One website I do like is http://www.verdoliso.be/nl/

Target Market(s)

Families

Industry/Entity Type

Travel

Number of Pages Required

5+ page

Font styles to use
Serif

Requirements
Must have
• The project must be responsive for mobile phones and tablets.
• Ability to search for holiday home holidays
• We want a natural colour scheme.
Nice to have
• A style we like is http://www.verdoliso.be/nl/
Should not have
• Do not use red as a colour for the website. Our logo is red so this is the only time we want this used.

```html
<!DOCTYPE html>
<html lang="en">
<head>
<meta charset="utf-8">
<title>Pinebrook Stays – Private Holiday Rentals</title>
<link href="https://fonts.googleapis.com/css2?family=Open+Sans:wght@400;600;700&family=Droid+Serif&display=swap" rel="stylesheet">
<style>
:root{
  --teal:#2f97a6;
  --teal-dark:#237b88;
  --green:#4caf50;
  --ink:#333;
  --muted:#8a8a8a;
  --line:#e3e3e3;
  --band:#f2f2f2;
  --dark:#2e2e2e;
  --darker:#232323;
  --white:#fff;
  --brand-red:#c9342b;
}
*{box-sizing:border-box;margin:0;padding:0}
html,body{width:1200px;height:2632px;overflow:hidden}
body{font-family:"Open Sans",Arial,sans-serif;color:var(--ink);background:var(--white);font-size:12px;position:relative}
a{color:inherit;text-decoration:none}
.wrap{width:1040px;margin:0 auto;position:relative}

/* header */
.topbar{height:118px}
.topbar .wrap{display:flex;justify-content:space-between;align-items:center;height:118px}
.brand{display:flex;align-items:center;gap:12px}
.brand-mark{width:34px;height:34px;background:var(--brand-red);border-radius:4px}
.brand-name{font-size:28px;font-weight:700;color:var(--brand-red)}
.brand-sub{font-size:11px;color:var(--muted);margin-top:2px}
.contact-line{display:flex;gap:26px;font-size:12px;color:#555}
.contact-line span{display:flex;align-items:center;gap:7px}
.ico{width:20px;height:20px;border-radius:50%;background:var(--teal);display:inline-flex;align-items:center;justify-content:center}

.nav{background:var(--teal);height:32px}
.nav ul{list-style:none;display:flex;height:32px;align-items:center}
.nav li{color:#fff;font-size:12px;padding:0 18px;height:32px;line-height:32px}
.nav li.active{background:var(--teal-dark)}

/* hero */
.hero{height:510px;position:relative;background:linear-gradient(180deg,#a9c6dd 0%,#c9d9c4 55%,#6e9a4b 100%)}
.hero-text{position:absolute;left:680px;top:210px;color:#fff;width:400px}
.hero-text h1{font-size:32px;font-weight:700;letter-spacing:1px;text-transform:uppercase}
.hero-text p{font-size:15px;line-height:22px;margin:10px 0 18px}
.btn{display:inline-block;background:var(--teal);color:#fff;font-size:11px;padding:8px 18px;border-radius:3px}
.dots{position:absolute;right:70px;bottom:14px;display:flex;gap:6px}
.dots i{width:8px;height:8px;border-radius:50%;background:rgba(255,255,255,.6)}
.dots i:first-child{background:#fff}

/* search */
.search{background:var(--band);height:100px;border-bottom:1px solid var(--line)}
.search .wrap{display:flex;align-items:center;height:100px;gap:10px}
.search-label{font-size:14px;color:var(--teal);width:200px}
.field{height:32px;background:#fff;border:1px solid #d8d8d8;border-radius:3px;font-size:11px;color:var(--muted);display:flex;align-items:center;padding:0 10px}
.search .btn{height:32px;line-height:16px}

/* section titles */
.sec-title{font-size:24px;color:#444;font-weight:400;margin-bottom:8px}
.sec-lead{font-size:12px;color:var(--muted);margin-bottom:26px}

/* cards */
.listing{padding-top:42px}
.cards{display:grid;grid-template-columns:repeat(4,1fr);gap:20px}
.card{border:1px solid var(--line);background:#fff;position:relative}
.card .photo{height:138px;margin:8px}
.card h3{font-size:14px;color:var(--teal);font-weight:600;margin:6px 12px 4px}
.card p{font-size:10px;color:var(--muted);line-height:15px;margin:0 12px 10px}
.card .meta{font-size:9px;color:#777;border-top:1px solid var(--line);margin:0 12px;padding:8px 0}
.card .sleeps{display:flex;gap:16px;font-size:10px;color:#666;border-top:1px solid var(--line);padding:8px 12px 10px}
.card .sleeps span{display:flex;gap:5px;align-items:center}
.badge{position:absolute;top:14px;right:14px;width:52px;height:52px;border-radius:50%;background:var(--teal);color:#fff;font-size:10px;text-align:center;display:flex;flex-direction:column;justify-content:center;line-height:13px}
.badge b{font-size:13px}

/* overview */
.overview{margin-top:66px;height:280px;background:linear-gradient(90deg,#1d1d1d 0%,#3a3a3a 60%,#262626 100%);position:relative;color:#fff}
.overview .photo{position:absolute;left:110px;top:50px;width:260px;height:200px;background:linear-gradient(135deg,#6b5a48,#b9a48a);transform:rotate(-8deg)}
.overview .text{position:absolute;left:440px;top:40px;width:640px}
.overview h2{font-size:26px;font-weight:400;margin-bottom:14px}
.overview p{font-size:12px;line-height:19px;color:#ccc;margin-bottom:16px}

/* late deals */
.deals{padding-top:40px}

/* lower */
.lower{margin-top:60px;border-top:1px solid var(--line);padding-top:26px}
.lower .wrap{display:grid;grid-template-columns:1fr 1fr 1fr;gap:36px}
.lower h4{font-size:14px;font-weight:600;margin-bottom:12px;color:#444}
.review-by{font-size:11px;color:var(--teal);margin-bottom:8px}
.lower p{font-size:11px;line-height:17px;color:var(--muted)}
.post-title{font-size:11px;color:var(--teal);margin-bottom:6px}
.post-date{font-size:10px;color:var(--teal);margin-top:10px}
.feed{border:1px solid var(--line)}
.feed-head{background:#4a6a8a;color:#fff;font-size:12px;font-weight:600;padding:8px 10px;display:flex;gap:8px;align-items:center}
.feed-head i{width:14px;height:14px;background:#fff;border-radius:2px;display:inline-block}
.feed-sub{font-size:10px;color:#666;padding:6px 10px;border-bottom:1px solid var(--line)}
.feed-row{display:flex;gap:8px;padding:6px 10px;font-size:10px;color:#666;align-items:center}
.feed-row .av{width:26px;height:26px;background:#c9c9c9;flex:none}

/* footer */
.footer{position:absolute;left:0;top:2372px;width:1200px;height:228px;background:var(--dark);color:#bbb}
.footer .wrap{display:grid;grid-template-columns:1.5fr 1fr 1fr 1fr 1fr;gap:30px;padding-top:28px}
.footer h5{color:#fff;font-size:12px;font-weight:600;margin-bottom:12px;text-transform:uppercase}
.footer li{list-style:none;font-size:10px;line-height:19px}
.footer p{font-size:10px;line-height:16px}
.footer .field{height:28px;margin:10px 0;background:#444;border-color:#555;color:#999}
.social li{display:flex;gap:8px;align-items:center}
.social i{width:14px;height:14px;border-radius:50%;background:#555;display:inline-block}
.copyright{position:absolute;left:0;top:2600px;width:1200px;height:32px;background:var(--darker);color:#999;font-size:10px;text-align:center;line-height:32px}

.side-tab{position:absolute;right:0;top:820px;width:22px;height:110px;background:var(--green);border-radius:3px 0 0 3px}
</style>
</head>
<body>

<header class="topbar">
  <div class="wrap">
    <div class="brand">
      <span class="brand-mark"></span>
      <div>
        <div class="brand-name">Pinebrook Stays</div>
        <div class="brand-sub">at Fernhollow Holiday Park</div>
      </div>
    </div>
    <div class="contact-line">
      <span><i class="ico"><svg width="10" height="10" viewBox="0 0 10 10"><path d="M2 1l2 2-1 1c.5 1.2 1.8 2.5 3 3l1-1 2 2-1.5 1.5C4 9 1 6 .5 2.5z" fill="#fff"/></svg></i>+44 (0)1632 960 418</span>
      <span><i class="ico"><svg width="10" height="10" viewBox="0 0 10 10"><rect x="1" y="2" width="8" height="6" fill="none" stroke="#fff"/><path d="M1 2l4 3 4-3" fill="none" stroke="#fff"/></svg></i>info@pinebrookstays.com</span>
    </div>
  </div>
</header>

<nav class="nav">
  <ul class="wrap">
    <li class="active">Home</li><li>New</li><li>Reviews</li><li>Caravans &amp; Lodges</li><li>Hire Lodges</li><li>Hire Holidays</li><li>Payment Plans</li><li>The Park</li><li>Local Attractions</li><li>Contact Us</li>
  </ul>
</nav>

<section class="hero" role="img" aria-label="Photo of a smiling couple outside a holiday lodge on a green lawn">
  <div class="hero-text">
    <h1>Private Holiday Rentals</h1>
    <p>Quality Lodge &amp; Caravan hire at Fernhollow Park. Book your break today.</p>
    <span class="btn">View More Info</span>
  </div>
  <div class="dots"><i></i><i></i><i></i></div>
</section>

<section class="search">
  <div class="wrap">
    <div class="search-label">Book Your Vacation in Few Minutes</div>
    <div class="field" style="width:190px">Select Lodge Name</div>
    <div class="field" style="width:140px">Check in Date</div>
    <div class="field" style="width:110px">Nights</div>
    <div class="field" style="width:130px">Guests</div>
    <span class="btn">Check Availability</span>
  </div>
</section>

<section class="listing">
  <div class="wrap">
    <h2 class="sec-title">List of Caravans and Lodges</h2>
    <p class="sec-lead">Find a holiday home that suits your family, from cosy caravans to spacious lodges with hot tubs and views over the park.</p>
    <div class="cards">
      <article class="card">
        <div class="photo" role="img" aria-label="Lodge living room interior" style="background:linear-gradient(135deg,#9b7a5a,#d7c4a6)"></div>
        <h3>The Alder</h3>
        <p>Open plan lounge with a bright kitchen and a decked terrace facing the lake.</p>
        <div class="meta">TYPE: CARAVAN &nbsp;|&nbsp; SLEEPS: 6 &nbsp;|&nbsp; LUXURY</div>
        <div class="sleeps"><span>Sleep 6</span><span>Bed 3</span></div>
      </article>
      <article class="card">
        <div class="photo" role="img" aria-label="Caravan lounge with sofas" style="background:linear-gradient(135deg,#a58b6c,#e2d6c2)"></div>
        <h3>The Winster</h3>
        <p>Warm family caravan with two shower rooms and a sheltered veranda.</p>
        <div class="meta">TYPE: CARAVAN &nbsp;|&nbsp; SLEEPS: 6 &nbsp;|&nbsp; LUXURY</div>
        <div class="sleeps"><span>Sleep 6</span><span>Bed 3</span></div>
      </article>
      <article class="card">
        <div class="photo" role="img" aria-label="Lodge lounge with fireplace" style="background:linear-gradient(135deg,#7c6a58,#cbb89c)"></div>
        <h3>The Bramble</h3>
        <p>Spacious lodge with an electric fire, dining area and private parking.</p>
        <div class="meta">TYPE: LODGE &nbsp;|&nbsp; SLEEPS: 6 &nbsp;|&nbsp; LUXURY</div>
        <div class="sleeps"><span>Sleep 6</span><span>Bed 3</span></div>
      </article>
      <article class="card">
        <div class="photo" role="img" aria-label="Lodge exterior with decking" style="background:linear-gradient(135deg,#6f7d5a,#c7c2a0)"></div>
        <h3>The Bramble II</h3>
        <p>Our newest lodge with a hot tub, garden views and a wide sun deck.</p>
        <div class="meta">TYPE: LODGE &nbsp;|&nbsp; SLEEPS: 6 &nbsp;|&nbsp; LUXURY</div>
        <div class="sleeps"><span>Sleep 6</span><span>Bed 3</span></div>
      </article>
    </div>
  </div>
</section>

<section class="overview">
  <div class="photo" role="img" aria-label="Photo of a modern lodge interior"></div>
  <div class="text">
    <h2>Overview of Company</h2>
    <p>We are a family run business offering quality lodge and caravan holidays at Fernhollow Park. Every home is cleaned, checked and prepared before you arrive, so you can relax from the moment you collect your keys. Booking with us is simple, safe and friendly, with a team on hand all year round.</p>
    <span class="btn">View More Info</span>
  </div>
</section>

<section class="deals">
  <div class="wrap">
    <h2 class="sec-title">Late Deals</h2>
    <p class="sec-lead">Grab a last minute break at a reduced price and enjoy a short stay with the whole family.</p>
    <div class="cards">
      <article class="card">
        <div class="photo" role="img" aria-label="Caravan bedroom" style="background:linear-gradient(135deg,#8d7861,#ddd0bb)"></div>
        <div class="badge"><b>£199</b>3 nights</div>
        <h3>The Hazel</h3>
        <p>Friday 1st September to Monday 4th September</p>
        <div class="sleeps"><span>Sleep 6</span><span>Bed 3</span></div>
      </article>
      <article class="card">
        <div class="photo" role="img" aria-label="Caravan kitchen" style="background:linear-gradient(135deg,#9a8873,#e6ddcd)"></div>
        <div class="badge"><b>£229</b>3 nights</div>
        <h3>The Glenmoor</h3>
        <p>Friday 8th September to Monday 11th September</p>
        <div class="sleeps"><span>Sleep 6</span><span>Bed 3</span></div>
      </article>
      <article class="card">
        <div class="photo" role="img" aria-label="Lodge living area" style="background:linear-gradient(135deg,#7d6c5b,#cdbda5)"></div>
        <div class="badge"><b>£249</b>3 nights</div>
        <h3>The Hazel</h3>
        <p>Friday 15th September to Monday 18th September</p>
        <div class="sleeps"><span>Sleep 6</span><span>Bed 3</span></div>
      </article>
      <article class="card">
        <div class="photo" role="img" aria-label="Lodge dining area" style="background:linear-gradient(135deg,#85735f,#d9cab2)"></div>
        <div class="badge"><b>£269</b>3 nights</div>
        <h3>The Glenmoor</h3>
        <p>Friday 22nd September to Monday 25th September</p>
        <div class="sleeps"><span>Sleep 6</span><span>Bed 3</span></div>
      </article>
    </div>
  </div>
</section>

<section class="lower">
  <div class="wrap">
    <div>
      <h4>Latest Review</h4>
      <div class="review-by">★ Sarah Miller stayed in The Alder</div>
      <p>"We had a wonderful week. The lodge was spotless, the beds were comfy and the children loved the park. The team were so helpful from start to finish and we will be back next summer."</p>
    </div>
    <div>
      <h4>Blog Feed</h4>
      <div class="post-title">New lodges arriving on the park this spring</div>
      <p>Two brand new lodges join our range this season, each with a hot tub, wide deck and open views across the lake.</p>
      <div class="post-date">Posted on 12 August 2017</div>
    </div>
    <div class="feed">
      <div class="feed-head"><i></i>Social Feed</div>
      <div class="feed-sub">Recent Activity</div>
      <div class="feed-row"><span class="av"></span>Pinebrook Stays shared new photos of the park.</div>
      <div class="feed-row"><span class="av"></span>Pinebrook Stays posted a late deal for September.</div>
      <div class="feed-row"><span class="av"></span>Pinebrook Stays added a new guest review.</div>
    </div>
  </div>
</section>

<footer class="footer">
  <div class="wrap">
    <div>
      <h5>Newsletter</h5>
      <p>Sign up for late deals, news and offers from the park.</p>
      <div class="field">Enter your email</div>
      <span class="btn">Subscribe Now</span>
    </div>
    <div>
      <h5>Contact Us</h5>
      <p>Fernhollow Holiday Park<br>Riverside Lane, Northdale</p>
      <p style="margin-top:8px">+44 (0)1632 960 418<br>info@pinebrookstays.com</p>
    </div>
    <div>
      <h5>Welcome</h5>
      <ul><li>Home</li><li>News</li><li>Caravans &amp; Lodges</li><li>Hire Holidays</li><li>Payment Plans</li><li>Late Deals</li></ul>
    </div>
    <div>
      <h5>Information</h5>
      <ul><li>The Park</li><li>Local Attractions</li><li>Guest Guide</li><li>Terms of Booking</li><li>Privacy Policy</li><li>Visitor Contact</li></ul>
    </div>
    <div>
      <h5>Follow Us</h5>
      <ul class="social"><li><i></i>Social Page</li><li><i></i>Updates</li><li><i></i>Photo Stream</li><li><i></i>Videos</li></ul>
    </div>
  </div>
</footer>
<div class="copyright">COPYRIGHT © PINEBROOKSTAYS.COM | ALL RIGHTS RESERVED</div>

<div class="side-tab"></div>
</body>
</html>
```